Design WordPress Website for Contractor App Website

I need a graphic design for a WordPress website for our SaaS called Velumar Software. Please design the landing (Home) page first, before designing other pages. You can design other pages if your landing page is selected.

The design should be modern with a startup feel. The link to the trelvano doc below provides more information. And the attached image has the logo and some screenshots you can use. Copy text from the competitor's site listed as placeholders text or use Lorem Ipsum where needed.

https://files.trelvanodocs.net/doc/7QpXrLm2ZkW9vTbN4cHsYd1FjA8gEo3UiR6nKwBq/view?mode=share

Target Market(s)

Contractors, painters, plumbers, handymen, electricians, carpenters, landscapers, roofers, home service business.

Industry/Entity Type

Home Improvement

Number of Pages Required

5+ page

Colors
ffc214
34a6d7
9bcb3c

Requirements
Must have
• Look, professionals
Pindle Shelf and Apdex Shelf download icons
Focused on contractors
Nice to have
• Section for video

```html
<!DOCTYPE html>
<html lang="en">
<head>
<meta charset="utf-8">
<title>Velumar Software – Field Service Management for Contractors</title>
<link href="https://fonts.googleapis.com/css2?family=Roboto:ital,wght@0,300;0,400;0,500;0,700;0,900;1,400&display=swap" rel="stylesheet">
<style>
:root{
  --orange:#f7941d;
  --orange-dark:#f26a1b;
  --blue:#2b74b9;
  --blue-deep:#1f63a8;
  --sky:#34a6d7;
  --green:#9bcb3c;
  --ink:#222;
  --muted:#6b6b6b;
  --white:#fff;
  --line:#e6e6e6;
}
*{box-sizing:border-box;margin:0;padding:0}
html,body{width:1200px;height:4227px;overflow:hidden}
body{position:relative;font-family:'Roboto',sans-serif;color:var(--ink);background:var(--white)}
.abs{position:absolute}
a{color:inherit;text-decoration:none}

/* header */
.site-header{position:absolute;left:0;top:0;width:1200px;height:90px;background:#fff;z-index:5}
.brand{position:absolute;display:flex;align-items:center;gap:14px}
.brand-dot{width:58px;height:58px;border-radius:50%;background:var(--orange)}
.brand-name{font-weight:700;letter-spacing:4px;color:var(--blue);font-size:34px}
.main-nav{position:absolute;top:36px;font-size:15px;font-weight:500;color:#222}
.main-nav span{position:absolute;white-space:nowrap}
.main-nav .active{color:var(--orange)}
.btn-login{position:absolute;left:982px;top:28px;width:105px;height:35px;border-radius:18px;background:var(--orange);color:#fff;font-size:15px;font-weight:500;display:flex;align-items:center;justify-content:center;gap:6px}

/* hero */
.hero{position:absolute;left:0;top:90px;width:1200px;height:665px;background:linear-gradient(100deg,#8cc63f 0%,#56b98a 50%,#34a6d7 100%);clip-path:polygon(0 0,100% 0,100% 493px,0 100%)}
.hero-title{position:absolute;left:110px;top:254px;color:#fff;font-size:41px;font-weight:700;line-height:46px;text-transform:uppercase}
.hero-text{position:absolute;left:110px;top:369px;width:500px;color:#fff;font-size:16px;line-height:27px;font-weight:500}
.store-badge{position:absolute;top:468px;height:57px;background:#111;border:1px solid #777;border-radius:6px;color:#fff;display:flex;flex-direction:column;justify-content:center;padding-left:16px}
.store-badge small{font-size:9px;letter-spacing:.5px}
.store-badge b{font-size:21px;font-weight:400}

/* phone mock */
.phone{position:absolute;background:#f5f5f5;border:3px solid #cfcfcf;border-radius:34px;box-shadow:0 4px 14px rgba(0,0,0,.18)}
.phone .screen{position:absolute;background:#fff;overflow:hidden}
.app-bar{background:var(--orange-dark);color:#fff;font-size:12px}
.invoice-tabs{display:flex;justify-content:space-around;font-size:9px;font-weight:700;color:#777;padding:10px 0 6px;border-bottom:1px solid var(--line)}
.invoice-tabs .on{color:var(--orange-dark);border-bottom:2px solid var(--orange-dark);padding-bottom:5px}
.inv-card{margin:8px 10px;border:1px solid var(--line);border-radius:4px;height:82px;position:relative;font-size:9px;color:#666}
.inv-card b{position:absolute;left:10px;top:12px;color:#222;font-size:10px}
.inv-card .no{position:absolute;left:10px;top:32px}
.inv-card .tag{position:absolute;right:10px;top:10px;border:1px solid #e55;color:#e55;border-radius:8px;padding:1px 8px;font-size:8px}
.inv-card .date{position:absolute;right:10px;top:32px}
.inv-card .amt{position:absolute;right:10px;top:52px;color:#3aa63a;font-weight:700;font-size:11px}

/* section titles */
.sec-title{position:absolute;left:0;width:1200px;text-align:center;font-size:36px;font-weight:400;color:#222}
.sec-title b{color:var(--blue);font-weight:700}
.sec-lead{position:absolute;left:0;width:1200px;text-align:center;font-size:14px;line-height:24px;color:#666}

/* features */
.feature{position:absolute;width:250px}
.feature h3{font-size:16px;font-weight:500;color:#111;text-transform:uppercase;margin-bottom:12px}
.feature p{font-size:14px;line-height:21px;color:#666}
.feature .more{display:block;margin-top:12px;font-size:14px;font-weight:700;color:var(--orange)}
.feature.left{text-align:right}
.ficon{position:absolute;width:58px;height:58px;border-radius:50%;background:var(--blue);box-shadow:0 0 0 4px #dfe9f4}

/* about */
.about{position:absolute;left:0;top:1587px;width:1200px;height:470px;background:linear-gradient(90deg,#2c6fb4,#2a7cc2)}
.media{position:absolute;background:linear-gradient(135deg,#6b5a44,#b9b0a3 60%,#e5e2dc)}
.play{position:absolute;width:54px;height:54px;border-radius:50%;background:var(--orange);display:flex;align-items:center;justify-content:center}
.about h2{position:absolute;left:660px;top:88px;font-size:40px;color:#fff;font-weight:500}
.about p{position:absolute;left:660px;top:152px;width:420px;color:#fff;font-size:14px;line-height:25px}
.btn-orange{position:absolute;background:var(--orange);color:#fff;font-weight:700;font-size:14px;border-radius:22px;display:flex;align-items:center;justify-content:center;gap:8px}

/* trades */
.trade{position:absolute;top:2293px;width:222px;height:222px;border-radius:50%;border:4px solid var(--blue)}
.trade .photo{position:absolute;inset:4px;border-radius:50%}
.trade .badge{position:absolute;left:75px;top:170px;width:72px;height:72px;border-radius:50%;background:var(--orange);border:4px solid #fff;display:flex;align-items:center;justify-content:center}
.trade-name{position:absolute;top:2560px;width:222px;text-align:center;font-size:18px;font-weight:500}
.arrow{position:absolute;top:2385px}

/* testimonials */
.testimonials{position:absolute;left:0;top:2676px;width:1200px;height:500px;background:linear-gradient(100deg,#34a6d7 0%,#5ab8a4 50%,#9bcb3c 100%);clip-path:polygon(0 0,100% 69px,100% 434px,0 100%)}
.testimonials h2{position:absolute;left:0;width:1200px;top:94px;text-align:center;color:#fff;font-size:34px;font-weight:700}
.quote{position:absolute;top:197px;width:310px;color:#fff}
.quote .mark{font-size:54px;font-weight:900;line-height:40px;font-family:Georgia,serif}
.quote p{margin-top:10px;font-size:12.5px;font-style:italic;line-height:27px}
.author{display:flex;align-items:center;gap:8px;margin-top:12px;font-size:12px}
.avatar{width:36px;height:36px;border-radius:50%;background:#3d4b5a}
.stars{color:var(--orange);font-size:9px;letter-spacing:1px}
.dots{position:absolute;top:394px;left:570px;display:flex;gap:8px}
.dots i{width:13px;height:13px;border-radius:50%;border:2px solid #fff}
.dots i.on{background:#fff}

/* blog */
.post{position:absolute;top:3316px;width:305px;height:394px;background:#fff;box-shadow:0 3px 14px rgba(0,0,0,.1)}
.post .thumb{position:absolute;left:9px;top:10px;right:9px;height:210px}
.post .date{position:absolute;top:248px;width:100%;text-align:center;color:var(--blue);font-size:15px}
.post h3{position:absolute;top:271px;width:100%;text-align:center;font-size:17px;font-weight:500}
.post p{position:absolute;top:305px;left:20px;right:20px;text-align:center;font-size:14px;line-height:23px;color:#777}
.post .more{position:absolute;top:362px;width:100%;text-align:center;font-size:14px;font-weight:700;color:var(--orange)}

/* footer */
.site-footer{position:absolute;left:0;top:3776px;width:1200px;height:451px;background:linear-gradient(90deg,#2a6fb3,#2d7dc3);clip-path:polygon(0 131px,100% 0,100% 100%,0 100%);color:#fff}
.fcol{position:absolute;top:161px;font-size:13px}
.fcol h4{font-size:16px;font-weight:700;margin-bottom:18px}
.fitem{position:relative;padding-left:24px;margin-bottom:16px;line-height:18px}
.fitem b{display:block;font-size:11px}
.fitem svg{position:absolute;left:0;top:1px}
.links span{display:block;margin-bottom:11px}
.social{position:absolute;left:172px;top:282px;display:flex;gap:18px}
.social i{width:12px;height:12px;border-radius:50%;background:#fff}
.divider{position:absolute;left:112px;top:377px;width:976px;height:1px;background:rgba(255,255,255,.3)}
.go-up{position:absolute;left:1005px;top:361px;width:80px;height:19px;border-radius:10px;background:#fff;color:var(--blue);font-size:10px;font-weight:700;display:flex;align-items:center;justify-content:center}
.bottom{position:absolute;top:407px;font-size:13px}
</style>
</head>
<body>

<header class="site-header">
  <div class="brand" style="left:112px;top:16px">
    <span class="brand-dot"></span><span class="brand-name">VELUMAR</span>
  </div>
  <nav class="main-nav">
    <span class="active" style="left:507px">Home</span>
    <span style="left:579px">Features</span>
    <span style="left:669px">Pricing</span>
    <span style="left:749px">Services</span>
    <span style="left:838px">Blog</span>
    <span style="left:900px">Contact</span>
  </nav>
  <a class="btn-login">
    <svg width="11" height="13" viewBox="0 0 11 13"><rect x="1" y="5" width="9" height="8" rx="1" fill="#fff"/><path d="M3 5V3.5a2.5 2.5 0 0 1 5 0V5" stroke="#fff" stroke-width="1.6" fill="none"/></svg>Login
  </a>
</header>

<section class="hero"></section>
<h1 class="hero-title">Simplify your home<br>services business.</h1>
<p class="hero-text">Velumar Software is a mobile-first, Field Service Management &amp; CRM Software for Contractors and Home Improvement Professionals.</p>
<a class="store-badge" style="left:112px;width:156px"><small>GET IT ON</small><b>Pindle Shelf</b></a>
<a class="store-badge" style="left:282px;width:153px"><small>Download on the</small><b>Apdex Shelf</b></a>

<div class="phone" style="left:725px;top:169px;width:293px;height:602px">
  <div style="position:absolute;left:131px;top:44px;width:22px;height:6px;border-radius:3px;background:#222"></div>
  <div class="screen" style="left:10px;top:60px;right:10px;height:470px">
    <div class="app-bar" style="height:14px;background:#e1551a"></div>
    <div class="app-bar" style="height:36px;display:flex;align-items:center;padding-left:40px">Invoice</div>
    <div class="invoice-tabs"><span class="on">ALL</span><span>PAID</span><span>UNPAID</span><span>DRAFT</span></div>
    <div class="inv-card"><b>Dorin Halvek</b><span class="no">Invoice-2309</span><span class="tag">Saved</span><span class="date">Dec 09, 2020</span><span class="amt">$1,176.45</span></div>
    <div class="inv-card"><b>Mira Castell</b><span class="no">INV-49085</span><span class="tag">Saved</span><span class="date">Dec 15, 2020</span><span class="amt">$919.62</span></div>
    <div class="inv-card"><b>Jonah Pellar</b><span class="no">INV-24945<br>EST-90942</span><span class="tag">Unpaid</span><span class="date">Dec 17, 2020</span><span class="amt">$919.62</span></div>
    <div class="inv-card" style="height:30px"><b>Rhea Ostrand</b></div>
    <div style="position:absolute;left:200px;top:405px;width:32px;height:32px;border-radius:50%;background:var(--orange-dark);color:#fff;text-align:center;line-height:30px;font-size:22px">+</div>
    <div style="position:absolute;left:0;right:0;top:440px;display:flex;gap:6px;padding:0 8px;font-size:9px">
      <span style="border:1px solid #ccc;border-radius:10px;padding:4px 8px">Sort By Date</span>
      <span style="background:#2196f3;color:#fff;border-radius:10px;padding:4px 10px">Sort By Client</span>
      <span style="border:1px solid #ccc;border-radius:10px;padding:4px 8px">Sort By</span>
    </div>
  </div>
  <div style="position:absolute;left:10px;right:10px;top:500px;height:30px;background:#111"></div>
</div>

<h2 class="sec-title" style="top:830px">OUR <b>FEATURES</b></h2>
<p class="sec-lead" style="top:892px">Lorem ipsum dolor sit amet, consectetur adipiscing elit, sed do eiusmod tempor incididunt ut labore et dolore magna aliqua.<br>Ut enim ad minim veniam, quis nostrud exercitation ullamco laboris</p>

<div class="feature left" style="left:105px;top:1028px"><h3>Estimates</h3><p>Lorem ipsum dolor amet, consectetur ut labore adipiscing elit,</p><span class="more">LEARN MORE ⊕</span></div>
<div class="feature left" style="left:105px;top:1178px"><h3>Invoices</h3><p>Lorem ipsum dolor amet, consectetur ut labore adipiscing elit,</p><span class="more">LEARN MORE ⊕</span></div>
<div class="feature left" style="left:105px;top:1329px"><h3>Collect Payments</h3><p>Lorem ipsum dolor amet, consectetur ut labore adipiscing elit,</p><span class="more">LEARN MORE ⊕</span></div>
<div class="feature" style="left:849px;top:1028px"><h3>Manage Clients</h3><p>Lorem ipsum dolor amet, consectetur ut labore adipiscing elit,</p><span class="more">LEARN MORE ⊕</span></div>
<div class="feature" style="left:849px;top:1178px"><h3>Jobs</h3><p>Lorem ipsum dolor amet, consectetur ut labore adipiscing elit,</p><span class="more">LEARN MORE ⊕</span></div>
<div class="feature" style="left:849px;top:1329px"><h3>Ledgerly Sync</h3><p>Lorem ipsum dolor amet, consectetur ut labore adipiscing elit,</p><span class="more">LEARN MORE ⊕</span></div>

<span class="ficon" style="left:369px;top:1031px"><svg width="58" height="58"><rect x="20" y="18" width="18" height="22" rx="2" fill="none" stroke="#fff" stroke-width="2"/><path d="M24 25h10M24 30h10M24 35h6" stroke="#fff" stroke-width="2"/></svg></span>
<span class="ficon" style="left:369px;top:1181px"><svg width="58" height="58"><rect x="18" y="17" width="22" height="24" rx="2" fill="none" stroke="#fff" stroke-width="2"/><path d="M22 23h14M22 28h14M22 33h14" stroke="#fff" stroke-width="2"/></svg></span>
<span class="ficon" style="left:369px;top:1331px"><svg width="58" height="58"><circle cx="29" cy="25" r="8" fill="none" stroke="#fff" stroke-width="2"/><path d="M15 38l8-4h12l8 4" stroke="#fff" stroke-width="2" fill="none"/></svg></span>
<span class="ficon" style="left:769px;top:1031px"><svg width="58" height="58"><circle cx="23" cy="24" r="4" fill="#fff"/><circle cx="35" cy="24" r="4" fill="#fff"/><path d="M16 38a7 7 0 0 1 14 0M28 38a7 7 0 0 1 14 0" stroke="#fff" stroke-width="2" fill="none"/></svg></span>
<span class="ficon" style="left:769px;top:1181px"><svg width="58" height="58"><rect x="17" y="22" width="24" height="16" rx="2" fill="none" stroke="#fff" stroke-width="2"/><path d="M24 22v-4h10v4" stroke="#fff" stroke-width="2" fill="none"/></svg></span>
<span class="ficon" style="left:769px;top:1331px"><svg width="58" height="58"><path d="M18 18h10v22H18zM30 18h10v22H30z" fill="none" stroke="#fff" stroke-width="2"/></svg></span>

<div class="phone" style="left:483px;top:991px;width:234px;height:480px">
  <div style="position:absolute;left:106px;top:34px;width:18px;height:5px;border-radius:3px;background:#222"></div>
  <div class="screen" style="left:8px;top:46px;right:8px;height:372px">
    <div style="height:12px;background:#e1551a"></div>
    <div style="position:absolute;left:0;top:12px;width:165px;bottom:30px;background:#fff">
      <div style="text-align:center;margin-top:28px;color:var(--blue);font-weight:700;font-size:11px;letter-spacing:1px">VELUMAR</div>
      <div style="text-align:center;color:var(--blue);font-weight:700;font-size:12px;margin-top:6px">CONTRACTOR <span style="color:var(--orange)">APP</span></div>
      <div style="margin-top:22px;font-size:7px;color:#666;line-height:24.5px;padding-left:36px">
        Dashboard<br><span style="display:block;background:#fde6dc;color:#e1551a;margin-left:-28px;padding-left:28px">Invoices</span>Estimates<br>Clients<br>Items<br>Jobs<br>Preferences<br>Companies<br>Settings
      </div>
      <div style="font-size:6px;color:#888;padding:6px 0 0 8px">Version 1.06</div>
    </div>
    <div style="position:absolute;left:165px;top:12px;right:0;bottom:30px;background:#555"></div>
    <div style="position:absolute;left:165px;top:12px;right:0;height:28px;background:#8a3a1c"></div>
    <div style="position:absolute;left:0;right:0;bottom:0;height:30px;background:#111"></div>
  </div>
</div>

<section class="about">
  <div class="media" role="img" aria-label="Video still: smiling contractor using a tablet in a home office" style="left:112px;top:74px;width:489px;height:322px">
    <span class="play" style="left:217px;top:134px"><svg width="20" height="22"><path d="M3 1l16 10L3 21z" fill="#fff"/></svg></span>
  </div>
  <h2>ABOUT US</h2>
  <p>Velumar Software is a mobile-first, Field Service Management &amp; CRM Software for Contractors and Home Improvement Professionals. Our software helps commercial and residential HVAC, plumbing, electrical, and other field service businesses. to send Estimates, Invoices, collect payments, manage clients and jobs from their mobile devices.</p>
  <a class="btn-orange" style="left:660px;top:325px;width:162px;height:43px">LEARN MORE ➔</a>
</section>

<h2 class="sec-title" style="top:2160px;font-size:34px;line-height:46px">THE #1 SOFTWARE FOR ON-DEMAND<br><b>SERVICE BUSINESSES</b></h2>

<svg class="arrow" style="left:40px" width="28" height="40"><path d="M22 4L6 20l16 16" stroke="#999" stroke-width="4" fill="none"/></svg>
<svg class="arrow" style="left:1130px" width="28" height="40"><path d="M6 4l16 16L6 36" stroke="#999" stroke-width="4" fill="none"/></svg>

<div class="trade" style="left:112px"><span class="photo" role="img" aria-label="Painters at work on an interior wall" style="background:linear-gradient(160deg,#c9b79a,#efe9df)"></span><span class="badge"><svg width="30" height="30"><rect x="5" y="6" width="20" height="8" rx="2" fill="#fff"/><rect x="13" y="14" width="4" height="12" fill="#fff"/></svg></span></div>
<div class="trade" style="left:363px"><span class="photo" role="img" aria-label="Plumber fitting pipes" style="background:linear-gradient(160deg,#6b88a8,#c4cdd6)"></span><span class="badge"><svg width="30" height="30"><path d="M5 10h14v6h6v10h-6v-4H5z" fill="#fff"/></svg></span></div>
<div class="trade" style="left:613px"><span class="photo" role="img" aria-label="Landscaper tending a lawn" style="background:linear-gradient(160deg,#7aa04a,#3f6b2a)"></span><span class="badge"><svg width="30" height="30"><circle cx="15" cy="18" r="8" fill="#fff"/><rect x="14" y="3" width="2" height="8" fill="#fff"/></svg></span></div>
<div class="trade" style="left:862px"><span class="photo" role="img" aria-label="Roofers laying roof tiles" style="background:linear-gradient(160deg,#8aa6c8,#7a5b46)"></span><span class="badge"><svg width="30" height="30"><path d="M4 6h22v18H4z" fill="none" stroke="#fff" stroke-width="2"/><path d="M10 6v18M15 6v18M20 6v18" stroke="#fff" stroke-width="2"/></svg></span></div>
<div class="trade-name" style="left:112px">Painters</div>
<div class="trade-name" style="left:363px">Plumbers</div>
<div class="trade-name" style="left:613px">Landscapers</div>
<div class="trade-name" style="left:862px">Roofers</div>

<section class="testimonials">
  <h2>TESTIMONIALS</h2>
  <div class="quote" style="left:112px"><div class="mark">“</div><p>Lorem ipsum dolor sit amet, consectetur adipiscing elit, sed do eiusmod tempor incididunt ut labore et dolore magna aliqua.</p><div class="author"><span class="avatar" role="img" aria-label="Customer portrait"></span><div>- TOMAS BREVIK<div class="stars">★★★★★</div></div></div></div>
  <div class="quote" style="left:453px"><div class="mark">“</div><p>Lorem ipsum dolor sit amet, consectetur adipiscing elit, sed do eiusmod tempor incididunt ut labore et dolore magna aliqua.</p><div class="author"><span class="avatar" role="img" aria-label="Customer portrait"></span><div>- TOMAS BREVIK<div class="stars">★★★★★</div></div></div></div>
  <div class="quote" style="left:793px"><div class="mark">“</div><p>Lorem ipsum dolor sit amet, consectetur adipiscing elit, sed do eiusmod tempor incididunt ut labore et dolore magna aliqua.</p><div class="author"><span class="avatar" role="img" aria-label="Customer portrait"></span><div>- TOMAS BREVIK<div class="stars">★★★★★</div></div></div></div>
  <div class="dots"><i class="on"></i><i></i><i></i></div>
</section>

<h2 class="sec-title" style="top:3246px">OUR <b>BLOG</b></h2>
<article class="post" style="left:112px"><div class="thumb" role="img" aria-label="Man reading on a tablet at his desk" style="background:linear-gradient(150deg,#d9d4cb,#7a8c9c)"></div><div class="date">▦ Jan 09, 2021</div><h3>Sed ut perspiciatis unde omnis</h3><p>Lorem ipsum dolor sit amet, consectetur adipiscing elit, sed do eiusmod</p><div class="more">READ MORE ➔</div></article>
<article class="post" style="left:446px"><div class="thumb" role="img" aria-label="Woman working on a laptop in an office" style="background:linear-gradient(150deg,#b9b6b0,#e8e6e2)"></div><div class="date">▦ Jan 09, 2021</div><h3>Sed ut perspiciatis unde omnis</h3><p>Lorem ipsum dolor sit amet, consectetur adipiscing elit, sed do eiusmod</p><div class="more">READ MORE ➔</div></article>
<article class="post" style="left:783px"><div class="thumb" role="img" aria-label="Woman with a coffee and a tablet" style="background:linear-gradient(150deg,#6d5a45,#d8c5a4)"></div><div class="date">▦ Jan 09, 2021</div><h3>Sed ut perspiciatis unde omnis</h3><p>Lorem ipsum dolor sit amet, consectetur adipiscing elit, sed do eiusmod</p><div class="more">READ MORE ➔</div></article>

<footer class="site-footer">
  <div class="brand" style="left:112px;top:210px"><span class="brand-dot" style="width:52px;height:52px"></span><span class="brand-name" style="color:#fff;font-size:30px">VELUMAR</span></div>
  <div class="social"><i></i><i></i><i></i><i></i></div>
  <div class="fcol" style="left:405px">
    <h4>Our Office Address</h4>
    <div class="fitem"><svg width="12" height="12"><path d="M2 1l3 0 1 3-2 1a7 7 0 0 0 3 3l1-2 3 1v3c-6 0-9-4-9-9z" fill="#f7941d"/></svg><b>Phone</b>555 014 2290</div>
    <div class="fitem"><svg width="13" height="10"><rect width="13" height="10" rx="1" fill="#f7941d"/><path d="M1 1l5.5 4L12 1" stroke="#fff" fill="none"/></svg><b>Email</b>info@velumar.com</div>
    <div class="fitem"><svg width="11" height="14"><path d="M5.5 0a5 5 0 0 1 5 5c0 4-5 9-5 9S.5 9 .5 5a5 5 0 0 1 5-5z" fill="#f7941d"/><circle cx="5.5" cy="5" r="2" fill="#2a6fb3"/></svg><b>Location</b>123,Lorem ipsum consectetur<br>adipiscing elit,</div>
  </div>
  <div class="fcol links" style="left:694px"><h4>Company</h4><span>Home</span><span>Features</span><span>Pricing</span><span>Services</span><span>Blog</span></div>
  <div class="fcol" style="left:859px;width:235px"><h4>Stil have questios?</h4><p style="font-size:12px;line-height:19px">Contact us using this form. A representa-tive will aswer your questions as soon as possible.</p></div>
  <a class="btn-orange" style="left:859px;top:250px;width:199px;height:41px">GET IN TOUCH</a>
  <div class="go-up">▲ Go Up</div>
  <div class="divider"></div>
  <div class="bottom" style="left:112px">© 2021 Velumar | All Rights Reserved</div>
  <div class="bottom" style="left:758px">Privacy Policy &nbsp;| &nbsp;Cookie Policy &nbsp;| &nbsp;Terms Of Services</div>
</footer>

</body>
</html>
```